Stationery Design Project for High End Wealth Management Firm

We need a stationery design for our high-end wealth management firm. Our clientele are affluent and our brand is built around providing investment services with world-class service.

The final concepts should provide a business card, letterhead, and envelope.

We like the idea of having text on the front and back and we MUST have black front and back business cards.
For the business card we have the following that needs to be included:
Company Logo & Tagline
Employee Name
Employee title
Employee Email
Website
2 seperate office cities, addresses, and phone numbers
Financial disclosure (small print)

Having black envelopes would be neat, but black is not a must for the envelopes.
Updates

Project Deadline Extended
Reason: To give the concept one more day of revisions.

Project Deadline Extended
Reason: To allow for more concepts and designs.

Target Market(s)

High Net Worth

Industry/Entity Type

Business

Requirements
Must have
• The following disclosure must be on the back of the card in small print:

Investment Advisory Services offered through Harrowfield Asset Partners LLC, a NFR Registered Investment Advisor. Vantory Wealth Management LLC is not affiliated with Harrowfield Asset Partners LLC.

Black business cards are also a must have.

Please utilize each of the 3 components of our logo in the design.

Please use our white background logo elements when designing our letterhead if you need them.
Nice to have
• Please use our company colors when designing. Utilize a combination of the elements of our logo that we have attached.

We are going to be printing our business cards on letterpress.

```html
<!DOCTYPE html>
<html lang="en">
<head>
<meta charset="utf-8">
<title>Vantory Wealth Management – Stationery</title>
<link rel="stylesheet" href="https://fonts.googleapis.com/css2?family=Cinzel:wght@400;600&family=Arimo:wght@400;700&display=swap">
<style>
  :root {
    --ink: #0b0b0b;
    --paper: #f6f6f6;
    --gold: #e9b84a;
    --gold-deep: #c8922a;
    --silver: #cfcfcf;
    --stage: #3b3b3b;
  }
  * { box-sizing: border-box; margin: 0; padding: 0; }
  html, body { width: 1200px; height: 900px; overflow: hidden; }
  body { background: var(--stage); font-family: "Arimo", Arial, sans-serif; position: relative; }

  .sheet { position: absolute; overflow: hidden; box-shadow: 0 8px 24px rgba(0,0,0,.45); }

  /* brand lockup */
  .brand { display: flex; align-items: center; gap: 8px; }
  .brand-dot { width: 22px; height: 22px; border-radius: 50%; background: var(--gold); flex: none; }
  .brand-name { font-family: "Cinzel", serif; font-weight: 400; color: var(--silver); font-size: 20px; letter-spacing: 1px; line-height: 1; }
  .tagline { color: var(--gold); font-size: 9px; margin-top: 6px; }

  .contact { font-size: 8.5px; line-height: 1.35; color: #fff; }
  .contact .office-label { color: var(--gold); }

  .header-band { background: var(--ink); border-bottom: 6px solid var(--gold); display: flex; justify-content: space-between; align-items: flex-end; }
  .wave { position: absolute; left: 0; bottom: 0; width: 100%; }
  .web { position: absolute; color: var(--gold); letter-spacing: 2px; font-size: 13px; }

  /* letterhead */
  .letterhead { left: 40px; top: 60px; width: 420px; height: 594px; background: var(--paper); }
  .letterhead .header-band { height: 120px; padding: 0 22px 16px; }
  .letterhead .web { right: 22px; bottom: 46px; }

  /* envelope */
  .envelope { left: 500px; top: 60px; width: 660px; height: 330px; background: var(--paper); }
  .envelope .header-band { height: 105px; padding: 0 24px 14px; }
  .address-window { position: absolute; left: 40px; top: 140px; width: 230px; height: 80px; border-radius: 10px; background: #e4e4e4; }
  .envelope .web { right: 24px; bottom: 130px; }

  /* cards */
  .card { top: 440px; width: 320px; height: 183px; background: var(--ink); }
  .card-front { left: 500px; display: flex; flex-direction: column; justify-content: center; padding: 0 30px; }
  .card-front .brand-name { font-size: 22px; }
  .card-back { left: 840px; padding: 18px 18px; }
  .card-back .brand-name { font-size: 14px; max-width: 170px; }
  .card-back .brand-dot { width: 16px; height: 16px; }
  .person { position: absolute; right: 18px; top: 56px; text-align: right; }
  .person-name { color: var(--gold); font-size: 10px; letter-spacing: 1px; }
  .person-title { color: #fff; font-size: 6.5px; margin-top: 2px; }
  .card-back .contact { position: absolute; left: 18px; top: 84px; font-size: 7px; }
  .card-back .web { right: 16px; bottom: 60px; font-size: 8px; letter-spacing: 1.5px; color: var(--ink); z-index: 1; }
</style>
</head>
<body>

<section class="sheet letterhead">
  <header class="header-band">
    <div>
      <div class="brand"><span class="brand-dot"></span><span class="brand-name">Vantory Wealth Management</span></div>
      <p class="tagline">Preferred Wealth Management for Select Individuals</p>
    </div>
  </header>
  <div class="contact" style="position:absolute;right:22px;top:18px;">
    <p><span class="office-label">Office 1</span> office cities, addresses</p>
    <p><span class="office-label">Office 2</span> office cities, addresses</p>
    <p>p : 555 214 0390 | 555 214 0391</p>
    <p>e : mellery@vantory.com</p>
  </div>
  <svg class="wave" width="420" height="170" viewBox="0 0 420 170" preserveAspectRatio="none" aria-hidden="true">
    <path d="M0 170 L0 150 C140 150 250 40 420 20 L420 170 Z" fill="#0b0b0b"/>
    <path d="M0 150 C150 150 250 55 420 30" fill="none" stroke="#f6f6f6" stroke-width="12"/>
    <path d="M0 128 C150 130 240 40 420 16" fill="none" stroke="#0b0b0b" stroke-width="2"/>
  </svg>
  <p class="web">www.vantory.com</p>
</section>

<section class="sheet envelope">
  <header class="header-band">
    <div>
      <div class="brand"><span class="brand-dot"></span><span class="brand-name">Vantory Wealth Management</span></div>
      <p class="tagline" style="color:#fff">Preferred Wealth Management for Select Individuals</p>
    </div>
    <div class="contact">
      <p><span class="office-label">Office 1</span> office cities, addresses</p>
      <p><span class="office-label">Office 2</span> office cities, addresses</p>
      <p>p : 555 214 0390 | 555 214 0391</p>
      <p>e : mellery@vantory.com</p>
    </div>
  </header>
  <div class="address-window"></div>
  <svg class="wave" width="660" height="210" viewBox="0 0 660 210" preserveAspectRatio="none" aria-hidden="true">
    <path d="M0 210 L0 150 C240 150 420 30 660 20 L660 210 Z" fill="#0b0b0b"/>
    <path d="M0 170 C260 170 430 40 660 40" fill="none" stroke="#f6f6f6" stroke-width="14"/>
    <path d="M0 130 C240 132 420 20 660 10" fill="none" stroke="#0b0b0b" stroke-width="2"/>
  </svg>
  <p class="web">www.vantory.com</p>
</section>

<section class="sheet card card-front">
  <div class="brand"><span class="brand-dot"></span><span class="brand-name">Vantory Wealth Management</span></div>
  <p class="tagline" style="color:#fff;font-size:9px;margin-top:10px;">Preferred Wealth Management for Select Individuals</p>
</section>

<section class="sheet card card-back">
  <div class="brand"><span class="brand-dot"></span><span class="brand-name">Vantory Wealth Management</span></div>
  <div class="person">
    <p class="person-name">MARTIN ELLERY</p>
    <p class="person-title">Position</p>
  </div>
  <div class="contact">
    <p><span class="office-label">Office 1</span> office cities, addresses</p>
    <p><span class="office-label">Office 2</span> office cities, addresses</p>
    <p>p : 555 214 0390 | 555 214 0391</p>
    <p>e : mellery@vantory.com</p>
  </div>
  <svg class="wave" width="320" height="100" viewBox="0 0 320 100" preserveAspectRatio="none" aria-hidden="true">
    <defs>
      <linearGradient id="goldSweep" x1="0" x2="1" y1="0" y2="0">
        <stop offset="0" stop-color="#c8922a"/>
        <stop offset="1" stop-color="#f2cf6e"/>
      </linearGradient>
    </defs>
    <path d="M0 100 L0 92 C120 92 200 14 320 8 L320 100 Z" fill="url(#goldSweep)"/>
    <path d="M0 100 C130 100 210 64 320 60" fill="none" stroke="#0b0b0b" stroke-width="6"/>
    <path d="M0 84 C120 84 200 6 320 2" fill="none" stroke="#e9b84a" stroke-width="1"/>
  </svg>
  <p class="web">www.vantory.com</p>
</section>

</body>
</html>
```